real esate business card with company logo and name

we need a business card design for a real esate company

The company name is Walsh & Brand Pty Ltd, and we have our logo designed and will upload. We want classic or moden feel. Black or white background. looks more textured. Should include folowinginformations
Owen Walsh and Lucy Brand
Sales Agents & Onsite Manager
p: 07 5948 2063
F: 07 5948 2174
M:0431 857 219
3/42 Marlow Crescent, FERNLEA QLD 4213

We want this business card looks professonal. Thank you in advance.

Industry/Entity Type

Real Estate Agent

Contact Information for Business Card

Owen Walsh and Lucy Brand
Onsite Manager & Sales Agents
p: 07 5948 2063
M:0431 857 219

Font styles to use
Serif

Colors
000000
fbfbfb
333333
959595

Requirements
Must have
• company logo and name, black or white back ground

```html
<!DOCTYPE html>
<html lang="en">
<head>
<meta charset="utf-8">
<title>Walsh &amp; Brand Pty Ltd — Business Card</title>
<link href="https://fonts.googleapis.com/css2?family=Open+Sans:wght@400;600&display=swap" rel="stylesheet">
<style>
  :root {
    --black: #000000;
    --paper: #fbfbfb;
    --charcoal: #333333;
    --mid-grey: #959595;
    --light-grey: #b4b4b4;
    --stage: #e6e6e6;
  }
  * { box-sizing: border-box; margin: 0; padding: 0; }
  html, body { width: 1200px; height: 900px; overflow: hidden; }
  body {
    background: var(--stage);
    font-family: "Open Sans", Arial, sans-serif;
    position: relative;
  }
  .card {
    position: absolute;
    left: 320px;
    width: 560px;
    height: 320px;
    overflow: hidden;
    box-shadow: 0 6px 18px rgba(0,0,0,0.18);
  }
  /* Back side */
  .card--back {
    top: 90px;
    background: linear-gradient(160deg, #2a2a2a 0%, #1a1a1a 55%, #111111 100%);
    display: flex;
    flex-direction: column;
    align-items: center;
    justify-content: center;
    gap: 18px;
  }
  .brand {
    display: flex;
    align-items: center;
    gap: 14px;
    font-weight: 600;
    letter-spacing: 0.12em;
    text-transform: uppercase;
  }
  .brand__square {
    width: 34px;
    height: 34px;
  }
  .card--back .brand { color: var(--paper); font-size: 26px; }
  .card--back .brand__square { background: var(--paper); }

  /* Front side */
  .card--front {
    top: 490px;
    background: var(--paper);
  }
  .card__bands {
    position: absolute;
    inset: 0;
    width: 560px;
    height: 320px;
  }
  .agents {
    position: absolute;
    left: 74px;
    top: 22px;
    color: var(--charcoal);
  }
  .agents__names { font-size: 19px; font-weight: 600; }
  .agents__role { font-size: 13px; margin-top: 1px; }
  .contact {
    position: absolute;
    left: 40px;
    top: 108px;
    color: var(--black);
    font-size: 14px;
    line-height: 1.35;
  }
  .contact__line { display: flex; align-items: center; gap: 8px; }
  .contact__line svg { width: 12px; height: 12px; fill: var(--charcoal); }
  .contact__address { margin-top: 14px; }
  .card--front .brand {
    position: absolute;
    right: 34px;
    top: 150px;
    color: var(--charcoal);
    font-size: 19px;
  }
  .card--front .brand__square { width: 28px; height: 28px; background: var(--mid-grey); }
</style>
</head>
<body>

  <section class="card card--back" aria-label="Card back">
    <div class="brand"><span class="brand__square"></span>Walsh &amp; Brand Pty Ltd.</div>
  </section>

  <section class="card card--front" aria-label="Card front">
    <svg class="card__bands" viewBox="0 0 560 320" aria-hidden="true">
      <polygon points="24,0 54,0 38,30 24,30" fill="var(--charcoal)"/>
      <polygon points="0,250 280,250 262,272 0,272" fill="var(--mid-grey)"/>
      <polygon points="278,270 560,270 560,304 254,304" fill="var(--charcoal)"/>
      <polygon points="0,272 262,272 254,282 0,282" fill="var(--light-grey)"/>
    </svg>

    <div class="agents">
      <p class="agents__names">Owen Walsh and Lucy Brand</p>
      <p class="agents__role">Onsite Manager &amp; Sales Agents</p>
    </div>

    <div class="contact">
      <p class="contact__line">
        <svg viewBox="0 0 24 24" aria-hidden="true"><path d="M3 9c0-3 4-5 9-5s9 2 9 5v2h-5V9c-1-1-7-1-8 0v2H3zM6 12h12l2 8H4z"/></svg>
        07 5948 2063
      </p>
      <p class="contact__line">
        <svg viewBox="0 0 24 24" aria-hidden="true"><path d="M7 1h10a2 2 0 0 1 2 2v18a2 2 0 0 1-2 2H7a2 2 0 0 1-2-2V3a2 2 0 0 1 2-2zm0 3v14h10V4zm5 15.5a1.2 1.2 0 1 0 0 2.4 1.2 1.2 0 0 0 0-2.4z"/></svg>
        0431 857 219
      </p>
      <p class="contact__address">3/42 Marlow Crescent,<br>FERNLEA QLD 4213</p>
    </div>

    <div class="brand"><span class="brand__square"></span>Walsh &amp; Brand Pty Ltd.</div>
  </section>

</body>
</html>
```